Dermatologist office in Brasilia. My with "target customers" are specially women.

I’m a dermatologist who works since 2006 in Brasilia. In 2017 I decided to change and improve my career. I decided to work more with cosmetics (Lumiqa and fillers), I still work with clinical and surgical dermatology.
Most of my patients are women but 20-30% are children and men.
I would like to see designs that use a butterfly and the color aquamarine with details in gold.

Industry/Entity Type

Cosmetics

Font styles to use
Sans Serif

Colors
33b8a4
87cfc6
cfeae6
85cae6

Requirements
Must have
• My project must have my name (Harumi Okeda) and my medical specialty (Dermatologista)
Nice to have
• The colors I prefer are aquamarine or Corvell Jade Tin.
• I also prefer a butterfly that means transformation and a new life.
• I prefer a sofisticated and also minimalist design.

```html
<!DOCTYPE html>
<html lang="pt">
<head>
<meta charset="UTF-8">
<title>Harumi Okeda – Dermatologista – Letterhead</title>
<link href="https://fonts.googleapis.com/css2?family=Questrial&display=swap" rel="stylesheet">
<style>
  :root {
    --backdrop: #b4d2f1;
    --paper: #ffffff;
    --aqua: #1fb5d6;
    --aqua-deep: #0f9cc4;
    --name-grey: #6d6e71;
    --text-grey: #7a7a7a;
    --tile: #e6e7e8;
    --tile-soft: #f1f2f2;
    --skin-light: #fbf3f0;
    --skin-mid: #f3e2dc;
  }
  * { margin: 0; padding: 0; box-sizing: border-box; }
  html, body { width: 1200px; height: 784px; overflow: hidden; }
  body {
    background: var(--backdrop);
    font-family: "Questrial", sans-serif;
    position: relative;
  }
  .letterhead {
    position: absolute;
    left: 350px; top: 38px;
    width: 500px; height: 708px;
    background: var(--paper);
    overflow: hidden;
    box-shadow: 0 6px 18px rgba(60, 100, 150, 0.18);
  }
  .corner-accent { position: absolute; }
  .corner-accent.top-left { left: 0; top: 0; }
  .corner-accent.bottom-right { right: 0; bottom: 0; }

  .tiles { position: absolute; }
  .tiles.header-tiles { right: 0; top: 0; }
  .tiles.footer-tiles { left: 0; bottom: 30px; }

  .brand {
    position: absolute;
    right: 34px; top: 46px;
    display: flex; align-items: center; gap: 12px;
  }
  .brand-mark {
    width: 30px; height: 30px;
    background: var(--aqua);
  }
  .brand-text { display: flex; flex-direction: column; align-items: flex-end; }
  .brand-name {
    font-size: 23px;
    color: var(--name-grey);
    letter-spacing: 0.3px;
    line-height: 1;
  }
  .brand-specialty {
    font-size: 12px;
    color: var(--aqua-deep);
    letter-spacing: 0.4px;
    margin-top: 4px;
  }

  .portrait-area {
    position: absolute;
    left: 110px; top: 250px;
    width: 330px; height: 400px;
    background:
      radial-gradient(ellipse 55% 50% at 55% 45%, var(--skin-mid) 0%, var(--skin-light) 45%, rgba(255,255,255,0) 75%);
  }

  .contact-bar {
    position: absolute;
    left: 16px; right: 60px; bottom: 12px;
    display: flex; align-items: center; gap: 5px;
    font-size: 6.8px;
    color: var(--text-grey);
    white-space: nowrap;
  }
  .contact-item { display: flex; align-items: center; gap: 3px; }
  .contact-icon { width: 9px; height: 9px; flex: none; }
</style>
</head>
<body>
  <main class="letterhead">
    <svg class="corner-accent top-left" width="90" height="60" viewBox="0 0 90 60" aria-hidden="true">
      <polygon points="0,0 90,0 0,60" fill="var(--aqua)" opacity="0.85"/>
      <polygon points="0,0 60,0 0,40" fill="#ffffff"/>
    </svg>
    <svg class="corner-accent bottom-right" width="70" height="40" viewBox="0 0 70 40" aria-hidden="true">
      <polygon points="70,0 70,40 0,40" fill="var(--aqua)" opacity="0.7"/>
    </svg>

    <svg class="tiles header-tiles" width="170" height="150" viewBox="0 0 170 150" aria-hidden="true">
      <rect x="40" y="10" width="60" height="46" fill="var(--tile-soft)"/>
      <rect x="110" y="0" width="60" height="34" fill="var(--tile-soft)"/>
      <rect x="40" y="90" width="70" height="54" fill="var(--tile)"/>
      <rect x="120" y="70" width="50" height="40" fill="var(--tile-soft)"/>
    </svg>

    <header class="brand">
      <div class="brand-text">
        <span class="brand-name">Harumi Okeda</span>
        <span class="brand-specialty">Dermatologista</span>
      </div>
      <div class="brand-mark"></div>
    </header>

    <div class="portrait-area" role="img" aria-label="Soft, faded portrait of a woman with smooth skin resting her hand at her chin"></div>

    <svg class="tiles footer-tiles" width="200" height="190" viewBox="0 0 200 190" aria-hidden="true">
      <rect x="0" y="80" width="70" height="60" fill="var(--tile)"/>
      <rect x="80" y="20" width="80" height="60" fill="var(--tile-soft)"/>
      <rect x="90" y="100" width="50" height="40" fill="var(--tile)"/>
      <rect x="40" y="140" width="60" height="45" fill="var(--tile-soft)"/>
      <rect x="20" y="0" width="45" height="30" fill="var(--tile-soft)"/>
    </svg>

    <footer class="contact-bar">
      <span class="contact-item">
        <svg class="contact-icon" viewBox="0 0 10 10"><circle cx="5" cy="5" r="5" fill="var(--aqua)"/><path d="M5 2.2a1.8 1.8 0 0 0-1.8 1.8C3.2 5.4 5 7.8 5 7.8S6.8 5.4 6.8 4A1.8 1.8 0 0 0 5 2.2z" fill="#fff"/></svg>
        Ed. Lumen, Sala 000, SHS Quadra 6, Brasília, DF 70316
      </span>
      <span class="contact-item">
        <svg class="contact-icon" viewBox="0 0 10 10"><circle cx="5" cy="5" r="5" fill="var(--aqua)"/><rect x="3.4" y="2.2" width="3.2" height="5.6" rx="0.6" fill="#fff"/></svg>
        (61) 3200-4417
      </span>
      <span class="contact-item">
        <svg class="contact-icon" viewBox="0 0 10 10"><circle cx="5" cy="5" r="5" fill="var(--aqua)"/><rect x="2.6" y="3" width="4.8" height="4" rx="0.5" fill="#fff"/></svg>
        (61) 98100-2263
      </span>
      <span class="contact-item">
        <svg class="contact-icon" viewBox="0 0 10 10"><circle cx="5" cy="5" r="5" fill="var(--aqua)"/><rect x="2.5" y="3.2" width="5" height="3.6" fill="#fff"/><path d="M2.5 3.2L5 5.2 7.5 3.2" stroke="var(--aqua)" stroke-width="0.6" fill="none"/></svg>
        contato@harumiokeda.med.br
      </span>
    </footer>
  </main>
</body>
</html>
```